32 x 24 Swinging Real Estate Yard Sign

We are looking to design a new sign for our business to focus on the remodeling of homes to sell. We are looking to have a yard sign that gets peoples attention and is informational. The headline will be "The Secret to Top Dollar? Remodel First.". We remodel homes for sellers with no up front cost, as they simply pay at closing. This link has more info, https://bramblecresthomes.com/Remodel
The message we want to convey to those seeing the sign is we are a one stop shop, who can renovate your home and sell it for no stress. We are licensed real estate agents and licensed contractors.
Both of these license numbers and info need to be on the design:
CADRE #02794613
Contractors License #1178524
Email: info@bramblecresthomes.com
Phone: (408)614-2907
I'll attach a sample sign we have for our agents normally as well as all brand art work.
• Pantone Colors
o #172A41
Dark blue
o #4381B1
Medium blue
o #6FA6CC
Light blue
Target Market(s)
Residential Real Estate Sellers
Industry/Entity Type
Real Estate
Colors
Designer to choose colors to be used in the design.

```html
<!DOCTYPE html>
<html lang="en">
<head>
<meta charset="utf-8">
<title>Bramblecrest Homes – Remodel First Yard Sign</title>
<link rel="stylesheet" href="https://fonts.googleapis.com/css2?family=Outfit:wght@300;700;800&family=Poppins:wght@600;700&display=swap">
<style>
  :root {
    --navy-deep: #0d1727;
    --navy: #1a2a43;
    --blue: #4381b1;
    --blue-muted: #36628a;
    --blue-light: #6fa6cc;
    --white: #ffffff;
  }
  * { margin: 0; padding: 0; box-sizing: border-box; }
  html, body { width: 916px; height: 1200px; overflow: hidden; background: var(--navy-deep); }
  .sign {
    position: relative;
    width: 916px;
    height: 1200px;
    background: var(--navy-deep);
    font-family: "Outfit", sans-serif;
    color: var(--white);
  }
  .sign__panel {
    position: absolute;
    left: 45px; top: 41px;
    width: 825px; height: 873px;
    background: var(--navy);
    overflow: hidden;
  }
  .phone-glow {
    position: absolute;
    left: 0; right: 0; bottom: 0; height: 115px;
    background: radial-gradient(ellipse 55% 100% at 50% 90%, rgba(67,129,177,0.55), rgba(67,129,177,0) 100%);
  }
  .brand {
    position: absolute;
    top: 196px; left: 0; right: 0;
    text-align: center;
    font-family: "Outfit", sans-serif;
    font-weight: 300;
    font-size: 42px;
    letter-spacing: 2px;
    color: var(--white);
  }
  .headline { position: absolute; left: 0; right: 0; text-align: center; line-height: 1; white-space: nowrap; }
  .headline--lead { top: 322px; font-size: 50px; font-weight: 300; }
  .headline--lead strong { font-weight: 800; }
  .headline--dollar { top: 372px; font-size: 80px; font-weight: 800; letter-spacing: -1px; }
  .headline--dollar .accent { color: var(--blue); }
  .headline--remodel { top: 450px; font-size: 128px; font-weight: 800; color: var(--blue); letter-spacing: -2px; }
  .headline--first { top: 572px; font-size: 212px; font-weight: 800; letter-spacing: -6px; }
  .contact-phone {
    position: absolute;
    left: 138px; top: 822px;
    display: flex; align-items: center; gap: 8px;
    font-family: "Poppins", sans-serif;
    font-weight: 700;
    font-size: 68px;
    line-height: 1;
    letter-spacing: 0.5px;
  }
  .contact-phone svg { flex: none; }
  .contact-email {
    position: absolute;
    left: 0; right: 0; top: 936px;
    display: flex; justify-content: center; align-items: center; gap: 14px;
    font-family: "Poppins", sans-serif;
    font-weight: 600;
    font-size: 38px;
  }
  .license {
    position: absolute;
    left: 50%; transform: translateX(-50%);
    display: flex;
    height: 46px;
    border-radius: 23px;
    overflow: hidden;
    font-family: "Poppins", sans-serif;
    font-weight: 700;
    font-size: 26px;
    line-height: 46px;
    white-space: nowrap;
  }
  .license__label { background: var(--blue-muted); padding: 0 16px 0 24px; }
  .license__number { background: var(--blue); padding: 0 24px 0 14px; }
  .license--cadre { top: 1009px; }
  .license--contractor { top: 1066px; }
</style>
</head>
<body>
  <main class="sign">
    <div class="sign__panel">
      <div class="phone-glow"></div>
    </div>

    <div class="brand">BRAMBLECREST HOMES</div>

    <h1 class="headline headline--lead">THE <strong>SECRET</strong> TO</h1>
    <p class="headline headline--dollar"><span class="accent">TOP</span> DOLLAR?</p>
    <p class="headline headline--remodel">REMODEL</p>
    <p class="headline headline--first">FIRST</p>

    <div class="contact-phone">
      <svg width="70" height="70" viewBox="0 0 70 70" aria-hidden="true">
        <circle cx="35" cy="35" r="35" fill="var(--blue)"/>
        <path d="M24 20c2-2 4-2 5 0l4 6c1 2 0 3-1 4l-2 2c2 4 5 7 9 9l2-2c1-1 2-2 4-1l6 4c2 1 2 3 0 5l-3 3c-3 3-10 0-17-7s-10-14-7-17z" fill="var(--white)"/>
        <path d="M39 22a10 10 0 0 1 9 9M40 16a16 16 0 0 1 14 14" stroke="var(--white)" stroke-width="3" fill="none" stroke-linecap="round"/>
      </svg>
      <span>(408)614-2907</span>
    </div>

    <div class="contact-email">
      <svg width="36" height="26" viewBox="0 0 36 26" aria-hidden="true">
        <rect x="1.5" y="1.5" width="33" height="23" fill="none" stroke="var(--blue)" stroke-width="3"/>
        <path d="M2 2l16 13L34 2M2 24l12-11M34 24L22 13" stroke="var(--blue)" stroke-width="3" fill="none"/>
      </svg>
      <span>info@bramblecresthomes.com</span>
    </div>

    <div class="license license--cadre">
      <span class="license__label">CADRE</span>
      <span class="license__number">#02794613</span>
    </div>
    <div class="license license--contractor">
      <span class="license__label">CONTRACTORS LICENSE</span>
      <span class="license__number">#1178524</span>
    </div>
  </main>
</body>
</html>
```